A start-up named "lumerova" - a clinical research organization needs a new PowerPoint design

We need a new PowerPoint Design (incl. business card and stationery design) for an early-stage start-up named "lumerova" seeking to build an ecosystem/ strategic partner alliances or consortium of committed and active collaborators to guide important components of the clinical trial.

Our ultimate goal is to avoid false neutrals – therapies that have not been and may never be evaluated in clinical trials due to the costs and/ or complexity.

The final design should highlight our patient-centric approach, innovative study design supported with the novel AI platform to make a stronger impact on patient lives.

Please see the attached brief for more details.
Updates

Requesting the proposals on color-coding, business-card designs, clinical research visuals, and icons as well as stationery design.

Target Market(s)

Pharma/ Biotech Executives
Medical Institutions
Clinical Trial Participants (Patients)

Colors
e34398

Requirements
Must have
• Use the Color Version of purple/ magenta logo

```html
<!DOCTYPE html>
<html lang="en">
<head>
<meta charset="utf-8">
<title>Lumerova – Business Card Variants</title>
<link rel="stylesheet" href="https://fonts.googleapis.com/css2?family=Ubuntu:wght@400;500;700&display=swap">
<style>
  :root {
    --bg: #ededed;
    --divider: #ffffff;
    --paper: #fafafa;
    --ink: #222222;
    --magenta: #a3307a;
    --magenta-bright: #c2147f;
    --magenta-deep: #93306a;
    --badge: #e2d0da;
  }
  * { box-sizing: border-box; margin: 0; padding: 0; }
  html, body { width: 1200px; height: 1096px; overflow: hidden; background: var(--divider); }
  body { position: relative; font-family: "Ubuntu", sans-serif; color: var(--ink); }

  .variant { position: absolute; width: 597px; height: 545px; background: var(--bg); }
  .variant--1 { left: 0; top: 0; }
  .variant--2 { left: 603px; top: 0; }
  .variant--3 { left: 0; top: 551px; }
  .variant--4 { left: 603px; top: 551px; }

  .badge { position: absolute; left: 29px; top: 30px; width: 100px; height: 100px; }
  .badge__number {
    position: absolute; inset: 0; display: flex; align-items: center; justify-content: center;
    font-weight: 700; font-size: 42px; color: var(--badge);
  }

  .card-front {
    position: absolute; left: 245px; top: 83px; width: 273px; height: 177px;
    background:
      linear-gradient(180deg, rgba(255,255,255,0.08), rgba(0,0,0,0.06)),
      linear-gradient(70deg, var(--magenta-bright) 0%, #b0206f 50%, var(--magenta-deep) 100%);
    display: flex; align-items: center; justify-content: center;
  }
  .wordmark { display: inline-block; font-weight: 700; letter-spacing: -0.5px; line-height: 1; }
  .card-front .wordmark { color: #ffffff; font-size: 32px; margin-top: -4px; }

  .card-back {
    position: absolute; left: 98px; top: 284px; width: 274px; height: 177px;
    background: var(--paper);
  }
  .card-back .wordmark { color: var(--magenta); font-size: 18px; }

  .band { position: absolute; left: 0; width: 100%; height: 7px; background: linear-gradient(90deg, var(--magenta-bright), var(--magenta-deep)); }
  .band--bottom { bottom: 0; }
  .band--top { top: 0; }

  .identity { position: absolute; left: 22px; top: 37px; }
  .identity__name { font-size: 12.5px; font-weight: 700; line-height: 14px; }
  .identity__role { font-size: 10px; color: var(--magenta); line-height: 12px; }
  .identity__rule { width: 83px; height: 1.5px; background: var(--magenta); margin-top: 3px; }

  .logo-slot { position: absolute; left: 174px; top: 30px; }

  .contacts { position: absolute; left: 22px; top: 105px; font-size: 6.7px; line-height: 7.7px; }
  .contacts__web { margin-top: 4px; }

  .company { position: absolute; left: 170px; width: 88px; top: 117px; text-align: center; font-size: 7.8px; line-height: 9px; }
  .company__name { font-size: 9.8px; font-weight: 700; line-height: 11px; }

  .variant--4 .identity { top: 44px; }
  .variant--4 .logo-slot { top: 37px; }
  .variant--4 .contacts { top: 106px; }
  .variant--4 .company { top: 118px; }

  .split .identity { left: 25px; top: 25px; }
  .split .identity__name { font-size: 9px; line-height: 10px; }
  .split .identity__role { font-size: 9px; line-height: 10.5px; color: var(--ink); }
  .split .contacts { left: 163px; top: 26px; }
  .split .contacts__web { margin-top: 5px; }
  .split .logo-slot { left: 25px; top: 117px; }
  .split .logo-slot .wordmark { font-size: 21px; }
  .split .company { left: 163px; top: 119px; width: auto; text-align: left; font-size: 6.5px; line-height: 7.7px; }
  .split .company__name { font-size: 6.7px; line-height: 7.7px; }
</style>
</head>
<body>

  <section class="variant variant--1">
    <div class="badge">
      <svg width="100" height="100" viewBox="0 0 100 100"><circle cx="50" cy="50" r="46" fill="none" stroke="var(--badge)" stroke-width="3"/><circle cx="50" cy="50" r="37" fill="none" stroke="var(--badge)" stroke-width="3"/></svg>
      <span class="badge__number">01</span>
    </div>
    <div class="card-front"><span class="wordmark">lumerova</span></div>
    <div class="card-back">
      <div class="identity">
        <p class="identity__name">Name Surname</p>
        <p class="identity__role">PhD</p>
        <p class="identity__role">Managing Partner</p>
        <div class="identity__rule"></div>
      </div>
      <div class="logo-slot"><span class="wordmark">lumerova</span></div>
      <div class="contacts">
        <p>O: +41 (0)12 345 60 00</p><p>P: +41 (0)12 345 67 89</p><p>M: +41 (0)98 765 43 21</p><p>F: +41 (0)12 345 60 01</p>
        <p class="contacts__web">name.surname@lumerova.ch</p><p>www.lumerova.ch</p>
      </div>
      <div class="company">
        <p class="company__name">Lumerova GmbH</p><p>Street name 1</p><p>9999 City name</p><p>Switzerland</p>
      </div>
      <div class="band band--bottom"></div>
    </div>
  </section>

  <section class="variant variant--2">
    <div class="badge">
      <svg width="100" height="100" viewBox="0 0 100 100"><circle cx="50" cy="50" r="46" fill="none" stroke="var(--badge)" stroke-width="3"/><circle cx="50" cy="50" r="37" fill="none" stroke="var(--badge)" stroke-width="3"/></svg>
      <span class="badge__number">02</span>
    </div>
    <div class="card-front"><span class="wordmark">lumerova</span></div>
    <div class="card-back split">
      <div class="identity">
        <p class="identity__name">Name Surname</p>
        <p class="identity__role">PhD</p>
        <p class="identity__role">Managing Partner</p>
      </div>
      <div class="contacts">
        <p>O: +41 (0)12 345 60 00</p><p>P: +41 (0)12 345 67 89</p><p>M: +41 (0)98 765 43 21</p><p>F: +41 (0)12 345 60 01</p>
        <p class="contacts__web">name.surname@lumerova.ch</p><p>www.lumerova.ch</p>
      </div>
      <div class="logo-slot"><span class="wordmark">lumerova</span></div>
      <div class="company">
        <p class="company__name">Lumerova GmbH</p><p>Street name 1</p><p>9999 City name</p><p>Switzerland</p>
      </div>
    </div>
  </section>

  <section class="variant variant--3">
    <div class="badge">
      <svg width="100" height="100" viewBox="0 0 100 100"><circle cx="50" cy="50" r="46" fill="none" stroke="var(--badge)" stroke-width="3"/><circle cx="50" cy="50" r="37" fill="none" stroke="var(--badge)" stroke-width="3"/></svg>
      <span class="badge__number">03</span>
    </div>
    <div class="card-front"><span class="wordmark">lumerova</span></div>
    <div class="card-back">
      <div class="identity">
        <p class="identity__name">Name Surname</p>
        <p class="identity__role">PhD</p>
        <p class="identity__role">Managing Partner</p>
        <div class="identity__rule"></div>
      </div>
      <div class="logo-slot"><span class="wordmark">lumerova</span></div>
      <div class="contacts">
        <p>O: +41 (0)12 345 60 00</p><p>P: +41 (0)12 345 67 89</p><p>M: +41 (0)98 765 43 21</p><p>F: +41 (0)12 345 60 01</p>
        <p class="contacts__web">name.surname@lumerova.ch</p><p>www.lumerova.ch</p>
      </div>
      <div class="company">
        <p class="company__name">Lumerova GmbH</p><p>Street name 1</p><p>9999 City name</p><p>Switzerland</p>
      </div>
    </div>
  </section>

  <section class="variant variant--4">
    <div class="badge">
      <svg width="100" height="100" viewBox="0 0 100 100"><circle cx="50" cy="50" r="46" fill="none" stroke="var(--badge)" stroke-width="3"/><circle cx="50" cy="50" r="37" fill="none" stroke="var(--badge)" stroke-width="3"/></svg>
      <span class="badge__number">04</span>
    </div>
    <div class="card-front"><span class="wordmark">lumerova</span></div>
    <div class="card-back">
      <div class="band band--top"></div>
      <div class="identity">
        <p class="identity__name">Name Surname</p>
        <p class="identity__role">PhD</p>
        <p class="identity__role">Managing Partner</p>
        <div class="identity__rule"></div>
      </div>
      <div class="logo-slot"><span class="wordmark">lumerova</span></div>
      <div class="contacts">
        <p>O: +41 (0)12 345 60 00</p><p>P: +41 (0)12 345 67 89</p><p>M: +41 (0)98 765 43 21</p><p>F: +41 (0)12 345 60 01</p>
        <p class="contacts__web">name.surname@lumerova.ch</p><p>www.lumerova.ch</p>
      </div>
      <div class="company">
        <p class="company__name">Lumerova GmbH</p><p>Street name 1</p><p>9999 City name</p><p>Switzerland</p>
      </div>
    </div>
  </section>

</body>
</html>
```